Crumb of Maple 2022- CW poster ads

Design for our Crumb of Maple Event
Designs 3 designs for Chirp Wall Banner, posts and social Media ads
Each can look the same just different subjects on each
1. Design We're Back!
The Crumb Of Maple Is Back!
Harlow Valley’s Premier Food, Wine and Brew Event
August 14th
Vendor and ticket info at https://brimfulmaplefq.com/

2. Vendors be a part of the event
The Crumb of Maple is Back!
August 14th 2020
Vendors sign up today at
Vendor info at https://brimfulmaplefq.com/

3. Sponsor info
The Crumb Of Maple
August 14th 2022
Check out our great Sponsorship opportunities
Sponsor info at https://brimfulmaplefq.com/

Target Market(s)

Foodies, wine and beer enthusists

Industry/Entity Type

Farm to fork, fresh in season and local

Colors
00AB8E
00BBA5
67D7C9
C6EFE9
E9F9F6

Requirements
Should not have
• no fast food looking photos

```html
<!DOCTYPE html>
<html lang="en">
<head>
<meta charset="utf-8">
<title>Crumb of Maple 2022 – Social Media Ads and Chirp Wall Banners</title>
<link rel="stylesheet" href="https://fonts.googleapis.com/css2?family=Oswald:wght@400;500;700&family=Bitter:wght@700&family=Roboto+Condensed:wght@400;700&display=swap">
<style>
  :root {
    --sheet-bg: #e7e7e7;
    --teal: #0f8f9c;
    --green: #14a383;
    --orange: #e9541f;
    --white: #ffffff;
    --kraft-light: #dcab72;
    --kraft-dark: #c28a4f;
    --pill: #ffffff;
  }
  * { box-sizing: border-box; margin: 0; padding: 0; }
  html, body { width: 800px; height: 1200px; overflow: hidden; }
  body {
    background: var(--sheet-bg);
    position: relative;
    font-family: "Roboto Condensed", Arial, sans-serif;
    color: var(--white);
  }

  .theme-back { --theme: var(--teal); }
  .theme-sponsor { --theme: var(--green); }
  .theme-vendor { --theme: var(--orange); }

  .piece { position: absolute; background: var(--theme); overflow: hidden; }
  .kraft {
    position: absolute; top: 0; right: 0; height: 100%;
    background: linear-gradient(160deg, var(--kraft-light), var(--kraft-dark));
  }
  .content {
    position: absolute; top: 0; left: 0; height: 100%;
    display: flex; flex-direction: column; align-items: center; justify-content: center;
    text-align: center;
  }
  .brand {
    display: flex; align-items: center; gap: 5px;
    font-family: "Roboto Condensed", Arial, sans-serif; font-weight: 700;
    color: var(--white); text-transform: uppercase; letter-spacing: .5px;
    white-space: nowrap;
  }
  .brand-dot { border-radius: 50%; background: var(--white); display: inline-block; }
  .headline {
    font-family: "Oswald", Arial, sans-serif; font-weight: 700;
    text-transform: uppercase; line-height: .95; white-space: nowrap;
  }
  .tagline {
    font-family: "Bitter", Georgia, serif; font-weight: 700;
    text-transform: uppercase; line-height: 1.05; white-space: nowrap;
  }
  .rule { height: 1px; background: rgba(255,255,255,.8); }
  .date { font-family: "Oswald", Arial, sans-serif; font-weight: 500; text-transform: uppercase; white-space: nowrap; }
  .sub { font-weight: 400; }
  .cta { font-weight: 700; text-transform: uppercase; letter-spacing: .4px; }
  .url {
    background: var(--pill); color: var(--theme); font-weight: 700;
    border-radius: 2px;
  }

  /* square social ad */
  .ad-square { left: 36px; width: 320px; height: 320px; }
  .ad-square .kraft { width: 96px; }
  .ad-square .content { width: 224px; padding: 0 14px; gap: 7px; }
  .ad-square .brand { font-size: 10px; }
  .ad-square .brand-dot { width: 14px; height: 14px; }
  .ad-square .headline { font-size: 46px; }
  .ad-square .headline.is-long { font-size: 25px; line-height: 1; }
  .ad-square .tagline { font-size: 17px; }
  .ad-square .rule { width: 170px; }
  .ad-square .date { font-size: 22px; }
  .ad-square .sub { font-size: 8px; }
  .ad-square .cta { font-size: 9px; }
  .ad-square .url { font-size: 8px; padding: 3px 8px; }

  /* chirp wall banner */
  .banner { left: 444px; width: 310px; height: 134px; }
  .banner .kraft { width: 104px; }
  .banner .content { width: 206px; padding: 0 10px; gap: 3px; }
  .banner .brand { position: absolute; top: 6px; left: 8px; font-size: 6px; }
  .banner .brand-dot { width: 8px; height: 8px; }
  .banner .headline { font-size: 19px; }
  .banner .headline.is-long { font-size: 14px; }
  .banner .tagline { font-size: 12px; }
  .banner .rule { width: 130px; }
  .banner .date { font-size: 12px; }
  .banner .sub { font-size: 6px; }
  .banner .url { font-size: 6px; padding: 2px 5px; }

  .label {
    position: absolute; font-family: "Oswald", Arial, sans-serif; font-weight: 500;
    font-size: 19px; letter-spacing: 1px; text-transform: uppercase; color: var(--theme);
    text-align: center;
  }
  .label-ad { left: 36px; width: 320px; }
  .label-banner { left: 444px; width: 310px; }
</style>
</head>
<body>

<section class="set theme-back">
  <article class="piece ad-square" style="top:24px">
    <div class="kraft" role="img" aria-label="Illustration of a wine bottle, bread and vines on kraft paper"></div>
    <div class="content">
      <div class="brand"><span class="brand-dot"></span>Crumb of Maple</div>
      <h1 class="headline">We're<br>Back</h1>
      <p class="tagline">The Crumb of<br>Maple is Back</p>
      <div class="rule"></div>
      <p class="date">August 14th</p>
      <p class="sub">Harlow Valley's Premier Food, Wine and Brew Event</p>
      <div class="rule"></div>
      <p class="cta">Vendor and ticket info at</p>
      <p class="url">brimfulmaplefq.com</p>
    </div>
  </article>
  <p class="label label-ad" style="top:350px">Social Media Ads</p>

  <article class="piece banner" style="top:110px">
    <div class="kraft" role="img" aria-label="Illustration of a wine bottle, bread and vines on kraft paper"></div>
    <div class="brand"><span class="brand-dot"></span>Crumb of Maple</div>
    <div class="content">
      <h2 class="headline">We're Back</h2>
      <p class="tagline">The Crumb of<br>Maple is Back</p>
      <div class="rule"></div>
      <p class="date">August 14th</p>
      <p class="url">brimfulmaplefq.com</p>
    </div>
  </article>
  <p class="label label-banner" style="top:252px">Chirp Wall Banner</p>
</section>

<section class="set theme-sponsor">
  <article class="piece ad-square" style="top:412px">
    <div class="kraft" role="img" aria-label="Illustration of a wine bottle, bread and vines on kraft paper"></div>
    <div class="content">
      <div class="brand"><span class="brand-dot"></span>Crumb of Maple</div>
      <h1 class="headline">Sponsor<br>Info</h1>
      <p class="tagline">The Crumb of<br>Maple is Back</p>
      <div class="rule"></div>
      <p class="date">August 14th 2022</p>
      <p class="sub">Check out our great Sponsorship opportunities</p>
      <div class="rule"></div>
      <p class="cta">Sponsor info at</p>
      <p class="url">brimfulmaplefq.com</p>
    </div>
  </article>
  <p class="label label-ad" style="top:738px">Social Media Ads</p>

  <article class="piece banner" style="top:500px">
    <div class="kraft" role="img" aria-label="Illustration of a wine bottle, bread and vines on kraft paper"></div>
    <div class="brand"><span class="brand-dot"></span>Crumb of Maple</div>
    <div class="content">
      <h2 class="headline">Sponsor Info</h2>
      <p class="tagline">The Crumb of<br>Maple is Back</p>
      <div class="rule"></div>
      <p class="date">August 14th 2022</p>
      <p class="sub">Check out our great Sponsorship opportunities</p>
    </div>
  </article>
  <p class="label label-banner" style="top:642px">Chirp Wall Banner</p>
</section>

<section class="set theme-vendor">
  <article class="piece ad-square" style="top:800px">
    <div class="kraft" role="img" aria-label="Illustration of a wine bottle, bread and vines on kraft paper"></div>
    <div class="content">
      <div class="brand"><span class="brand-dot"></span>Crumb of Maple</div>
      <h1 class="headline is-long">Vendors be a<br>part of the event</h1>
      <p class="tagline">The Crumb of<br>Maple is Back</p>
      <div class="rule"></div>
      <p class="date">August 14th 2020</p>
      <p class="sub">Vendors sign up today at</p>
      <div class="rule"></div>
      <p class="cta">Vendor info at</p>
      <p class="url">brimfulmaplefq.com</p>
    </div>
  </article>
  <p class="label label-ad" style="top:1126px">Social Media Ads</p>

  <article class="piece banner" style="top:890px">
    <div class="kraft" role="img" aria-label="Illustration of a wine bottle, bread and vines on kraft paper"></div>
    <div class="brand"><span class="brand-dot"></span>Crumb of Maple</div>
    <div class="content">
      <h2 class="headline is-long">Vendors be a part<br>of the event</h2>
      <p class="tagline">The Crumb of<br>Maple is Back</p>
      <div class="rule"></div>
      <p class="date">August 14th 2020</p>
      <p class="url">brimfulmaplefq.com</p>
    </div>
  </article>
  <p class="label label-banner" style="top:1032px">Chirp Wall Banner</p>
</section>

</body>
</html>
```